New Webpage for High Class Expert Witness Services Company

We are looking for a minimalist design for a webpage that just has our logo and an entry form offer to connect with one of our Liaisons.
The entry form should just ask for Name, Email, Contact Info and Description of Project.

Company Name is: The Marlowe Crest Advisory Services

Number of Pages Required

1 page

```html
<!DOCTYPE html>
<html lang="en">
<head>
<meta charset="utf-8">
<title>The Marlowe Crest Advisory Services — Connect</title>
<link rel="stylesheet" href="https://fonts.googleapis.com/css2?family=IM+Fell+Double+Pica&family=Poppins:wght@400;600;700&display=swap">
<style>
  :root {
    --ink: #131313;
    --panel: #121212;
    --paper: #ffffff;
    --field: #ececec;
    --placeholder: #a9a9a9;
    --icon: #8e8e8e;
    --light: #e6e6e6;
  }
  * { box-sizing: border-box; margin: 0; padding: 0; }
  html, body { width: 1200px; height: 788px; overflow: hidden; background: var(--paper); }
  body { position: relative; font-family: "Poppins", sans-serif; color: var(--ink); }

  .brand-panel {
    position: absolute; left: 0; top: 0; width: 680px; height: 788px;
    background: var(--panel); overflow: hidden;
  }
  .brand-name {
    position: absolute; left: 0; top: 140px; width: 680px;
    display: flex; align-items: center; justify-content: center; gap: 16px;
    font-family: "IM Fell Double Pica", serif; font-size: 30px;
    color: var(--light); letter-spacing: 1px; text-transform: uppercase; line-height: 1.15;
    text-align: left;
  }
  .brand-name .mark { width: 14px; height: 14px; background: var(--light); flex: none; }
  .hero-photo {
    position: absolute; left: 0; top: 338px; width: 680px; height: 450px;
    background:
      radial-gradient(ellipse at 55% 45%, #3a3a3a 0%, #262626 40%, transparent 75%),
      linear-gradient(180deg, #121212 0%, #222 25%, #1c1c1c 70%, #151515 100%);
  }
  .copyright {
    position: absolute; left: 120px; top: 731px;
    font-size: 11px; font-weight: 600; color: #f2f2f2; letter-spacing: 0.1px;
  }

  .contact { position: absolute; left: 766px; top: 0; width: 348px; }
  .contact-title {
    position: absolute; top: 142px; left: 0; width: 380px;
    font-family: "IM Fell Double Pica", serif; font-weight: 400;
    font-size: 32px; line-height: 34px; color: var(--ink); text-transform: uppercase;
  }
  .field-label {
    position: absolute; left: 0; font-size: 10px; font-weight: 600; text-transform: uppercase;
  }
  .field {
    position: absolute; left: 0; width: 348px; height: 40px;
    background: var(--field); border-radius: 6px;
    display: flex; align-items: center; padding: 0 16px;
    font-size: 11px; color: var(--placeholder);
  }
  .field svg { position: absolute; right: 16px; top: 50%; transform: translateY(-50%); }
  .field--area { height: 108px; align-items: flex-start; }
  .field--area svg { top: 20px; }
  .submit {
    position: absolute; left: 0; top: 598px; width: 348px; height: 42px;
    background: var(--ink); border-radius: 6px; color: #fff;
    display: flex; align-items: center; justify-content: center;
    font-size: 11px; font-weight: 600; text-transform: uppercase;
  }
  .submit svg { position: absolute; right: 22px; top: 50%; transform: translateY(-50%); }
</style>
</head>
<body>
  <section class="brand-panel">
    <div class="hero-photo" role="img" aria-label="Dark monochrome photograph of a soldier in tactical gear aiming a rifle"></div>
    <div class="brand-name"><span class="mark"></span><span>The Marlowe Crest<br>Advisory Services</span></div>
    <p class="copyright">© COPYRIGHT 2026 ALL RIGHTS RESERVED</p>
  </section>

  <section class="contact">
    <h1 class="contact-title">The Marlowe Crest<br>Advisory Services</h1>

    <label class="field-label" style="top:234px">Name</label>
    <div class="field" style="top:250px">Johny
      <svg width="10" height="11" viewBox="0 0 10 11" fill="var(--icon)"><circle cx="5" cy="3" r="2.6"/><path d="M0 11c0-3 2.2-4.6 5-4.6S10 8 10 11z"/></svg>
    </div>

    <label class="field-label" style="top:306px">Email</label>
    <div class="field" style="top:322px">Johny@email.com
      <svg width="11" height="9" viewBox="0 0 11 9" fill="var(--icon)"><rect x="0" y="0" width="11" height="9" rx="1"/><path d="M0.5 1l5 3.5 5-3.5" stroke="#ececec" stroke-width="1" fill="none"/></svg>
    </div>

    <label class="field-label" style="top:379px">Contact Info</label>
    <div class="field" style="top:394px">+081 123456 789
      <svg width="10" height="10" viewBox="0 0 10 10" fill="var(--icon)"><path d="M2 0.5l1.6 2.3-1 1c.6 1.3 1.6 2.3 2.9 2.9l1-1L9.5 7.3 8.4 9.3C4.3 9 1 5.7.7 1.6z"/></svg>
    </div>

    <label class="field-label" style="top:452px">Description of Project</label>
    <div class="field field--area" style="top:467px">
      <svg width="13" height="12" viewBox="0 0 13 12" fill="var(--icon)"><ellipse cx="8" cy="4.5" rx="4.5" ry="3.8"/><path d="M9 7.5l1.5 2-3-1.4z"/><ellipse cx="3.6" cy="6.5" rx="3.2" ry="2.7" opacity=".7"/></svg>
    </div>

    <div class="submit">Connect with us
      <svg width="12" height="12" viewBox="0 0 12 12" fill="#fff"><path d="M12 0L0 5.2l3.6 1.5L10 2 4.6 7.6V11.5l2-2.6 2.8 1.6z"/></svg>
    </div>
  </section>
</body>
</html>
```